Brell Stone Company Business Cards

Front and Back Business Card - logo and text setup - cool design. I need workable photoshop or illustrator files so I can setup each employee card with design that is created
Updates

Hi everyone, thank you for the great entries. Please no more white and blue cards - there are so many already - black and silver only now please. thanks!

Target Market(s)

Construction Industry - Facility Managers

Industry/Entity Type

Construction

Contact Information for Business Card

I really like contemporary simplistic looks - clean neat....not opposed to seeing some black backrounds

Requirements
Must have
• Logo/website address with design on front only - www.brellstone-example.com (logo attached)
• Back:
• Name/Title/Company Address/Phone/email address
Nice to have
• Cool design
Should not have
• Nothing gimmicky like Fire or Water - since we are a Fire Protection company - it has all been done

```html
<!DOCTYPE html>
<html lang="en">
<head>
<meta charset="utf-8">
<title>Brell Stone Company – Business Cards</title>
<link href="https://fonts.googleapis.com/css2?family=Lato:wght@400;700;900&display=swap" rel="stylesheet">
<style>
  :root {
    --backdrop: #121212;
    --card: #262626;
    --accent: #e8402c;
    --silver: #c8c8c8;
    --white: #f4f4f4;
    --muted: #d9d9d9;
    --rule: #8a8a8a;
  }
  * { box-sizing: border-box; margin: 0; padding: 0; }
  html, body { width: 1200px; height: 912px; overflow: hidden; }
  body {
    background: var(--backdrop);
    font-family: "Lato", sans-serif;
    display: flex;
    flex-direction: column;
    align-items: center;
    justify-content: center;
    gap: 48px;
  }
  .card {
    position: relative;
    width: 640px;
    height: 366px;
    background: var(--card);
    overflow: hidden;
  }
  .card__band {
    position: absolute;
    left: 0; right: 0; bottom: 0;
    height: 12px;
    background: var(--accent);
  }
  .wordmark {
    display: flex;
    align-items: center;
    gap: 12px;
    font-weight: 900;
    letter-spacing: -1px;
    line-height: 1;
  }
  .wordmark__square { display: block; background: var(--accent); }

  /* Front */
  .card--front .wordmark {
    position: absolute;
    left: 0; right: 0; top: 118px;
    justify-content: center;
    font-size: 64px;
    color: var(--silver);
  }
  .card--front .wordmark__square { width: 22px; height: 22px; background: var(--silver); }
  .card--front .website {
    position: absolute;
    left: 0; right: 0; top: 262px;
    text-align: center;
    font-size: 17px;
    color: var(--white);
    letter-spacing: 0.3px;
  }

  /* Back */
  .card--back .wordmark {
    position: absolute;
    left: 40px; top: 176px;
    font-size: 40px;
    color: var(--white);
  }
  .card--back .wordmark__square { width: 16px; height: 16px; }
  .divider {
    position: absolute;
    left: 318px; top: 60px;
    width: 1px; height: 230px;
    background: var(--rule);
  }
  .contact {
    position: absolute;
    left: 346px; top: 72px;
    color: var(--muted);
  }
  .contact__name { font-size: 23px; font-weight: 700; color: var(--white); }
  .contact__title { font-size: 15px; color: var(--accent); margin-top: 4px; }
  .contact__address { font-size: 14px; line-height: 1.45; margin-top: 18px; }
  .contact__list { list-style: none; margin-top: 16px; font-size: 14px; line-height: 1.5; }
  .contact__list li { display: flex; align-items: center; gap: 10px; }
  .contact__list svg { width: 13px; height: 13px; flex: none; }
</style>
</head>
<body>
  <section class="card card--front" aria-label="Card front">
    <div class="wordmark">Brell Stone<span class="wordmark__square"></span></div>
    <p class="website">www.brellstone-example.com</p>
    <div class="card__band"></div>
  </section>

  <section class="card card--back" aria-label="Card back">
    <div class="wordmark">Brell Stone<span class="wordmark__square"></span></div>
    <div class="divider"></div>
    <div class="contact">
      <p class="contact__name">Dana Mercer Hollis</p>
      <p class="contact__title">President</p>
      <p class="contact__address">48 Harbor Point Road<br>Millbrook, NY 10021</p>
      <ul class="contact__list">
        <li>
          <svg viewBox="0 0 16 16" aria-hidden="true"><path fill="#e8402c" d="M3.5 1l2.5 3-1.5 1.6c.9 2 2.4 3.5 4.4 4.4L10.5 8.5l3 2.5-1.2 2.8C7 14 2 9 2.2 3.7z"/></svg>
          (555) 014-2290
        </li>
        <li>
          <svg viewBox="0 0 16 16" aria-hidden="true"><rect x="1" y="3" width="14" height="10" fill="#e8402c"/><path d="M1 3.5l7 5.5 7-5.5" fill="none" stroke="#262626" stroke-width="1.4"/></svg>
          info@brellstone-example.com
        </li>
        <li>
          <svg viewBox="0 0 16 16" aria-hidden="true"><circle cx="8" cy="8" r="7" fill="#e8402c"/><path d="M1 8h14M8 1c-3 3.5-3 10.5 0 14M8 1c3 3.5 3 10.5 0 14" fill="none" stroke="#262626" stroke-width="1.1"/></svg>
          www.brellstone-example.com
        </li>
      </ul>
    </div>
    <div class="card__band"></div>
  </section>
</body>
</html>
```